Basic / Quick Business Card

Quick easy design project!

Need a one sided basic business card that matches font & style of brand and bottle label for our gourmet condiment, Brindle Harrow Sauce. Brindle Harrow Sauce is sold in specialty retail, gourmet groceries and appears on chef-driven restaurant menus, so the target market is a high end, gourmet, artisan-made food-loving customer.

Files Included:
Sauce Bottle Label
Brindle Harrow Sauce Round Logos

**About the logos - the logo may be used in a circle or alone vertically as on side of the bottle label**

Layout of Card:
May be vertical or horizontal based on designer ideas.

Logo usage (in circle vs. stand alone vertical logo) is up to designers descretion as well.

Reverse side of business card will be various high end / professional product photos / food shots using us.kelbo.com system. **Designer on this project will NOT design a reserve for the card.**

Paper that will be used for printing:
Kelbo Standard - it's a WHITE paper, but we use a cream background on Brindle Harrow Sauce branding, so please take this into account on design to stay brand consistent.

Elements & Copy for Card:
1. Logo in either script horizontal or vertical version
2. Copy: "Artisan Made - Small Batch"
3. Name - Wes Dorrance
4. Title - Creator
5. Phone - xxx.xxx.xxxx
6. xxxx@brindleharrow.com
7. URL: brindleharrowsauce.com
8. Social Media: @getbrindleharrow on Quillo / Pagora / Lumigrid

Please provide final files in Illustrator or InDesign format.

```html
<!DOCTYPE html>
<html lang="en">
<head>
<meta charset="utf-8">
<title>Brindle Harrow Sauce – Business Card</title>
<link rel="stylesheet" href="https://fonts.googleapis.com/css2?family=Open+Sans:ital,wght@0,400;0,700;1,400&display=swap">
<style>
  :root {
    --stage: #e9e6e1;
    --card-yellow: #f2b310;
    --ink: #231f20;
    --cream: #f4efd9;
    --ring: #2a2526;
  }
  * { margin: 0; padding: 0; box-sizing: border-box; }
  html, body {
    width: 1200px; height: 804px; overflow: hidden;
    background: var(--stage);
    font-family: "Open Sans", Arial, sans-serif;
    color: var(--ink);
  }
  .card {
    position: absolute; left: 80px; top: 105px;
    width: 1040px; height: 594px;
    background: var(--card-yellow);
    overflow: hidden;
  }
  .card__swoosh { position: absolute; inset: 0; width: 100%; height: 100%; }
  .brand-seal {
    position: absolute; left: 105px; top: 172px;
    width: 240px; height: 240px; border-radius: 50%;
    background: var(--cream);
    border: 8px solid var(--ring);
    display: flex; align-items: center; justify-content: center;
    text-align: center;
  }
  .brand-seal__name {
    font-weight: 700; font-size: 31px; line-height: 1.12;
    color: var(--ink);
  }
  .tagline {
    position: absolute; left: 120px; top: 452px; width: 320px;
    text-align: center; font-style: italic; font-size: 22px; line-height: 1.25;
  }
  .contact {
    position: absolute; right: 48px; top: 52px;
    text-align: right;
  }
  .contact__name { font-weight: 700; font-size: 36px; line-height: 1.1; }
  .contact__title { font-size: 27px; line-height: 1.2; margin-bottom: 66px; }
  .contact__line {
    display: flex; justify-content: flex-end; align-items: center; gap: 9px;
    font-size: 24px; line-height: 1.6;
  }
  .contact__line svg { width: 20px; height: 20px; flex: none; }
  .social {
    position: absolute; right: 48px; top: 432px; text-align: right;
  }
  .social__heading { font-size: 23px; margin-bottom: 6px; }
  .social__list { display: flex; justify-content: flex-end; gap: 14px; list-style: none; }
  .social__item { display: flex; align-items: center; gap: 5px; font-size: 16px; }
  .social__dot { width: 14px; height: 14px; border-radius: 50%; background: var(--ink); }
</style>
</head>
<body>
<main class="card">
  <svg class="card__swoosh" viewBox="0 0 1040 594" aria-hidden="true">
    <path d="M582 0 L612 0 C520 150 545 420 780 594 L738 594 C500 430 480 170 582 0 Z" fill="var(--ink)"/>
    <path d="M548 90 C500 250 540 450 700 594 L690 594 C520 460 480 270 548 90 Z" fill="var(--ink)"/>
  </svg>

  <div class="brand-seal">
    <span class="brand-seal__name">Brindle<br>Harrow<br>Sauce</span>
  </div>

  <p class="tagline">sweet &amp; spicy<br>made in mississippi<br>Artisan Made - Small Batch</p>

  <section class="contact">
    <h1 class="contact__name">Wes Dorrance</h1>
    <p class="contact__title">Creator</p>
    <p class="contact__line">
      <svg viewBox="0 0 20 20"><circle cx="10" cy="10" r="9" fill="none" stroke="currentColor" stroke-width="1.6"/><path d="M7 5 l2 0 l1 3 l-1.5 1 q1 2 3 3 l1-1.5 l3 1 l0 2 q-6 0-8.5-8.5z" fill="currentColor"/></svg>
      123-456-7890
    </p>
    <p class="contact__line">
      <svg viewBox="0 0 20 20"><rect x="2" y="5" width="16" height="11" rx="1" fill="currentColor"/><path d="M2.5 6 L10 11 L17.5 6" fill="none" stroke="var(--card-yellow)" stroke-width="1.4"/></svg>
      wdorrance@brindleharrow.com
    </p>
    <p class="contact__line">
      <svg viewBox="0 0 20 20"><circle cx="10" cy="10" r="8" fill="none" stroke="currentColor" stroke-width="1.8"/><ellipse cx="10" cy="10" rx="3.5" ry="8" fill="none" stroke="currentColor" stroke-width="1.4"/><path d="M2 10 H18" stroke="currentColor" stroke-width="1.4"/></svg>
      www.brindleharrowsauce.com
    </p>
  </section>

  <section class="social">
    <p class="social__heading">Follow Us On</p>
    <ul class="social__list">
      <li class="social__item"><span class="social__dot"></span>Pagora</li>
      <li class="social__item"><span class="social__dot"></span>Quillo</li>
      <li class="social__item"><span class="social__dot"></span>Lumigrid</li>
    </ul>
  </section>
</main>
</body>
</html>
```